Varnex Consulting Business card design.

See our website www.varnexconsulting.example which will give you a good idea of what we are about. The font is called 'Play'.

I'd like a standout business card in keeping with the themes and branding on the website

Target Market(s)

professionals. HR directors

Industry/Entity Type

Business

Contact Information for Business Card

Varnex Consulting PO Box 3172 Merrowdale NSW 2291 1300 485 193 Gavin Threlkeld Principal email: career@varnexconsulting.example ABN: 71203948865

Font styles to use
Other font styles liked:
• Play

Requirements
Must have
• Must have same design colours and branding as website.
• On back I'd prefer a list of the things we do which appears below the name at the header on the website

```html
<!DOCTYPE html>
<html lang="en">
<head>
<meta charset="utf-8">
<title>Varnex Consulting – Business Card</title>
<link href="https://fonts.googleapis.com/css2?family=Play:wght@400;700&display=swap" rel="stylesheet">
<style>
  :root {
    --navy: #132a3e;
    --blue: #2a93e0;
    --white: #ffffff;
    --paper: #f7f8f9;
    --ink: #132a3e;
    --backdrop: #e9eaec;
  }
  * { margin: 0; padding: 0; box-sizing: border-box; }
  html, body { width: 1200px; height: 1200px; overflow: hidden; }
  body {
    background: var(--backdrop);
    font-family: 'Play', sans-serif;
    position: relative;
  }
  .card {
    position: absolute;
    left: 200px;
    width: 800px;
    height: 472px;
    overflow: hidden;
  }
  .card--front { top: 110px; background: var(--navy); }
  .card--back { top: 620px; background: var(--paper); }

  .brand-name {
    position: absolute;
    left: 0; right: 0;
    text-align: center;
    font-size: 60px;
    font-weight: 400;
    letter-spacing: 1px;
    line-height: 1;
    white-space: nowrap;
  }
  .card--front .brand-name { top: 146px; color: var(--white); }
  .services {
    position: absolute;
    left: 0; right: 0;
    text-align: center;
    color: var(--blue);
    font-size: 17px;
    letter-spacing: 3px;
    white-space: nowrap;
  }
  .card--front .services { top: 216px; }
  .services .sep { margin: 0 5px; letter-spacing: 0; }

  .front-web {
    position: absolute;
    top: 392px; left: 0; right: 0;
    display: flex; justify-content: center; align-items: center;
    gap: 14px;
    color: var(--white);
    font-size: 20px;
  }
  .front-web .dash { width: 38px; height: 3px; background: var(--blue); border-radius: 50%; }
  .accent { color: var(--blue); }

  .header-band {
    position: absolute;
    left: 0; top: 0;
    width: 800px; height: 118px;
    background: var(--navy);
    border-bottom: 6px solid var(--blue);
  }
  .person { position: absolute; right: 38px; top: 30px; text-align: right; }
  .person__name { color: var(--white); font-size: 27px; font-weight: 700; line-height: 1.1; }
  .person__role { color: var(--white); font-size: 18px; margin-top: 8px; }

  .contact { position: absolute; left: 54px; top: 146px; color: var(--ink); font-size: 20px; }
  .contact__row { display: flex; align-items: center; height: 27px; }
  .contact__icon { width: 18px; height: 16px; margin-right: 22px; fill: var(--blue); }
  .contact__address { margin-top: 4px; height: 27px; line-height: 27px; }
  .contact__abn { margin-top: 18px; }
  .contact__abn .label { color: var(--blue); }

  .card--back .brand-name { top: 336px; left: 54px; right: auto; text-align: left; color: var(--ink); }
  .card--back .services { top: 405px; left: 54px; right: auto; text-align: left; }
</style>
</head>
<body>

<section class="card card--front">
  <div class="brand-name">VARNEX CONSULTING</div>
  <div class="services">Search &amp; Select<span class="sep">|</span>Career<span class="sep">|</span>Coaching<span class="sep">|</span>Leadership<span class="sep">|</span>Outplacement</div>
  <div class="front-web">
    <span class="dash"></span>
    <span>www.<span class="accent">varnexconsulting</span>.example</span>
    <span class="dash"></span>
  </div>
</section>

<section class="card card--back">
  <div class="header-band"></div>

  <div class="person">
    <div class="person__name">Gavin Threlkeld</div>
    <div class="person__role">Principal</div>
  </div>

  <div class="contact">
    <div class="contact__row">
      <svg class="contact__icon" viewBox="0 0 18 16"><path d="M2,4 C2,1 16,1 16,4 L16,6 L12,6 L12,4.5 L6,4.5 L6,6 L2,6 Z M4,7 L14,7 L16,14 L2,14 Z"/></svg>
      <span>1300 485 193</span>
    </div>
    <div class="contact__row">
      <svg class="contact__icon" viewBox="0 0 18 16"><circle cx="9" cy="8" r="7" fill="none" stroke="var(--blue)" stroke-width="1.6"/><ellipse cx="9" cy="8" rx="3" ry="7" fill="none" stroke="var(--blue)" stroke-width="1.4"/><path d="M2,8 H16 M3.5,4.5 H14.5 M3.5,11.5 H14.5" stroke="var(--blue)" stroke-width="1.2"/></svg>
      <span>www.<span class="accent">varnexconsulting</span>.example</span>
    </div>
    <div class="contact__row">
      <svg class="contact__icon" viewBox="0 0 18 16"><rect x="1" y="3" width="16" height="11"/><path d="M1,3 L9,10 L17,3" fill="none" stroke="var(--paper)" stroke-width="1.4"/></svg>
      <span>career@varnexconsulting.example</span>
    </div>
    <div class="contact__address">PO Box 3172 Merrowdale NSW 2291</div>
    <div class="contact__abn"><span class="label">ABN:</span> 71203948865</div>
  </div>

  <div class="brand-name">VARNEX CONSULTING</div>
  <div class="services">Search &amp; Select<span class="sep">|</span>Career<span class="sep">|</span>Coaching<span class="sep">|</span>Leadership<span class="sep">|</span>Outplacement</div>
</section>

</body>
</html>
```